Harbor Crestline (Business Card Design)

Need business cards designed. Something modern, chic, and sleek. Mabye the back of the card should be the navy blue that is in the logo and then just the logo on the back.

Target Market(s)

Those in the hotel, office, and renovation industry

Contact Information for Business Card

1. Logo 2. Dorian Fenwick 3. CEO/Founder 4. Phone: (833) HarbCre / (833) 427-2731 5. Email: dorian@theharborcrestline.com 6. Website: www.theharborcrestline.com

Font styles to use
Other font styles liked:
• Look at the logo font and base the font for everything else off of that.

Colors
0054AA
0677BA
7BADD7
CADEEF
E8F1F8

Requirements
Must have
• Colors that are associated in the logo
Nice to have
• Sleek modern clean and chic design.

```html
<!DOCTYPE html>
<html lang="en">
<head>
<meta charset="UTF-8">
<title>Harbor Crestline — Business Cards</title>
<link rel="stylesheet" href="https://fonts.googleapis.com/css2?family=Montserrat:wght@400;500;600&display=swap">
<style>
  :root {
    --navy: #0d1a42;
    --gold: #c9a24a;
    --white: #ffffff;
    --stage-dark: #333333;
    --stage-light: #ffffff;
    --divider: rgba(255,255,255,0.06);
  }
  * { margin: 0; padding: 0; box-sizing: border-box; }
  html, body { width: 1200px; height: 2887px; overflow: hidden; }
  body { font-family: "Montserrat", sans-serif; background: var(--stage-light); position: relative; }

  .stage { position: absolute; left: 0; width: 1200px; }
  .stage--dark { top: 0; height: 1440px; background: var(--stage-dark); }
  .stage--light { top: 1440px; height: 1447px; background: var(--stage-light); }

  .card {
    position: absolute; left: 130px; width: 940px; height: 537px;
    background: var(--navy); overflow: hidden;
  }
  .stage--dark .card { box-shadow: 0 22px 18px -14px rgba(0,0,0,0.75); }
  .stage--light .card { box-shadow: 0 6px 28px rgba(0,0,0,0.28); }

  .card--front-a { top: 111px; }
  .card--back-a  { top: 752px; }
  .card--front-b { top: 157px; }
  .card--back-b  { top: 797px; }

  /* front: centered name mark */
  .brand {
    position: absolute; display: flex; flex-direction: column; align-items: center;
    color: var(--white); font-weight: 600; text-transform: uppercase; text-align: center;
  }
  .brand__square { width: 22px; height: 22px; background: var(--gold); margin-bottom: 26px; }
  .brand__name { line-height: 1.08; }

  .card--front .brand { left: 0; right: 0; top: 150px; }
  .card--front .brand__name { font-size: 58px; letter-spacing: 4px; }

  /* back: name mark left, details right */
  .card--back .brand { left: 36px; width: 400px; top: 150px; }
  .card--back .brand__square { width: 16px; height: 16px; margin-bottom: 22px; }
  .card--back .brand__name { font-size: 42px; letter-spacing: 3px; }

  .divider {
    position: absolute; left: 469px; top: 83px; width: 2px; height: 370px;
    background: var(--divider);
  }
  .details { position: absolute; left: 493px; top: 122px; }
  .details__name { color: var(--white); font-size: 44px; font-weight: 600; line-height: 1; }
  .details__title { color: var(--gold); font-size: 26px; font-weight: 500; margin-top: 22px; }
  .contact { list-style: none; margin-top: 34px; }
  .contact__item {
    display: flex; align-items: center; gap: 12px;
    color: var(--white); font-size: 21.5px; font-weight: 400; height: 26px; margin-bottom: 27px;
  }
  .contact__icon { width: 26px; height: 26px; flex: none; }
</style>
</head>
<body>

<section class="stage stage--dark">
  <article class="card card--front card--front-a">
    <div class="brand">
      <span class="brand__square"></span>
      <span class="brand__name">Harbor<br>Crestline</span>
    </div>
  </article>

  <article class="card card--back card--back-a">
    <div class="brand">
      <span class="brand__square"></span>
      <span class="brand__name">Harbor<br>Crestline</span>
    </div>
    <span class="divider"></span>
    <div class="details">
      <h1 class="details__name">Dorian Fenwick</h1>
      <p class="details__title">CEO/Founder</p>
      <ul class="contact">
        <li class="contact__item">
          <svg class="contact__icon" viewBox="0 0 26 26"><circle cx="13" cy="13" r="11.5" fill="none" stroke="#c9a24a" stroke-width="1.5"/><path d="M9 7.5l2.2 2.4-1.2 1.6c.8 1.8 2.2 3.2 4 4l1.6-1.2 2.4 2.2-1.4 1.8c-4-.6-7.6-4.2-8.2-8.2z" fill="none" stroke="#c9a24a" stroke-width="1.3" stroke-linejoin="round"/></svg>
          (833) HarbCre / (833) 427-2731
        </li>
        <li class="contact__item">
          <svg class="contact__icon" viewBox="0 0 26 26"><circle cx="13" cy="13" r="11.5" fill="none" stroke="#c9a24a" stroke-width="1.5"/><rect x="7.5" y="9" width="11" height="8" fill="none" stroke="#c9a24a" stroke-width="1.3"/><path d="M7.5 9l5.5 4.5L18.5 9" fill="none" stroke="#c9a24a" stroke-width="1.3"/></svg>
          dorian@theharborcrestline.com
        </li>
        <li class="contact__item">
          <svg class="contact__icon" viewBox="0 0 26 26"><circle cx="13" cy="13" r="11.5" fill="none" stroke="#c9a24a" stroke-width="1.5"/><circle cx="13" cy="13" r="6" fill="none" stroke="#c9a24a" stroke-width="1.2"/><ellipse cx="13" cy="13" rx="2.6" ry="6" fill="none" stroke="#c9a24a" stroke-width="1.1"/><path d="M7 13h12" stroke="#c9a24a" stroke-width="1.1"/></svg>
          www.theharborcrestline.com
        </li>
      </ul>
    </div>
  </article>
</section>

<section class="stage stage--light">
  <article class="card card--front card--front-b">
    <div class="brand">
      <span class="brand__square"></span>
      <span class="brand__name">Harbor<br>Crestline</span>
    </div>
  </article>

  <article class="card card--back card--back-b">
    <div class="brand">
      <span class="brand__square"></span>
      <span class="brand__name">Harbor<br>Crestline</span>
    </div>
    <span class="divider"></span>
    <div class="details">
      <h2 class="details__name">Dorian Fenwick</h2>
      <p class="details__title">CEO/Founder</p>
      <ul class="contact">
        <li class="contact__item">
          <svg class="contact__icon" viewBox="0 0 26 26"><circle cx="13" cy="13" r="11.5" fill="none" stroke="#c9a24a" stroke-width="1.5"/><path d="M9 7.5l2.2 2.4-1.2 1.6c.8 1.8 2.2 3.2 4 4l1.6-1.2 2.4 2.2-1.4 1.8c-4-.6-7.6-4.2-8.2-8.2z" fill="none" stroke="#c9a24a" stroke-width="1.3" stroke-linejoin="round"/></svg>
          (833) HarbCre / (833) 427-2731
        </li>
        <li class="contact__item">
          <svg class="contact__icon" viewBox="0 0 26 26"><circle cx="13" cy="13" r="11.5" fill="none" stroke="#c9a24a" stroke-width="1.5"/><rect x="7.5" y="9" width="11" height="8" fill="none" stroke="#c9a24a" stroke-width="1.3"/><path d="M7.5 9l5.5 4.5L18.5 9" fill="none" stroke="#c9a24a" stroke-width="1.3"/></svg>
          dorian@theharborcrestline.com
        </li>
        <li class="contact__item">
          <svg class="contact__icon" viewBox="0 0 26 26"><circle cx="13" cy="13" r="11.5" fill="none" stroke="#c9a24a" stroke-width="1.5"/><circle cx="13" cy="13" r="6" fill="none" stroke="#c9a24a" stroke-width="1.2"/><ellipse cx="13" cy="13" rx="2.6" ry="6" fill="none" stroke="#c9a24a" stroke-width="1.1"/><path d="M7 13h12" stroke="#c9a24a" stroke-width="1.1"/></svg>
          www.theharborcrestline.com
        </li>
      </ul>
    </div>
  </article>
</section>

</body>
</html>
```